KR Appraisals website redesign

I would like to refresh my existing website of www.krappraisals-example.com with new graphics, look and feel, as well as updated structure and wording. Content and layout changes have been uploaded to this project Brief.

My existing website has a dark feel. I am now looking for a light and energetic feel. Financial Services is my industry, so the website should be reflect that. I would also like to reflect the concepts of Trust, Service and Expertise.

The website must be serious and upmarket.

Target Market(s)

Corporate board members, CFO's, treasurers and controllers
Auditors, tax advisors, private equity and venture capital asset managers, investors, tax authorities

Industry/Entity Type

Financial Service

Coding

Coded - Design and coding required

Number of Pages Required

5+ page

Font styles to use
Sans Serif
Other font styles liked:
• Designer can choose another modern font

Colors
0355a3
3277b5
85acd3
eaf1f7
f37122
f68d4d
9bcb3c
acd037
cadf82

Requirements
Must have
• Good hi resolution pictures that convey "Finance", "Trust", "Service" or "Expertise".
• An anti-bot (such as Captcha) mechanism in the contact form.
Should not have
• Must not have all content on one rolling screen.

```html
<!DOCTYPE html>
<html lang="en">
<head>
<meta charset="utf-8">
<title>KR Appraisals – Business &amp; Intellectual Property Valuations</title>
<link href="https://fonts.googleapis.com/css2?family=Montserrat:wght@600;700;800&family=Open+Sans:wght@400;600;700&display=swap" rel="stylesheet">
<style>
:root{
  --blue:#0355a3;
  --blue-mid:#3277b5;
  --blue-light:#85acd3;
  --blue-pale:#eaf1f7;
  --orange:#f37122;
  --orange-light:#f68d4d;
  --green:#9bcb3c;
  --green-mid:#acd037;
  --green-pale:#cadf82;
  --ink:#222;
  --grey-text:#6b6f75;
  --section-grey:#efefef;
  --footer:#2b2b2b;
  --white:#fff;
}
*{margin:0;padding:0;box-sizing:border-box}
html,body{width:1200px;height:2288px;overflow:hidden}
body{font-family:"Open Sans",Arial,sans-serif;color:var(--ink);background:var(--white);position:relative}

/* header + hero */
.hero{position:absolute;left:0;top:0;width:1200px;height:640px;
  background:linear-gradient(100deg,#f3f3f1 0%,#e9e9e6 45%,#d9dad6 75%,#c9cbc6 100%)}
.hero-photo{position:absolute;left:600px;top:120px;width:520px;height:500px;
  background:radial-gradient(ellipse at 55% 40%,rgba(120,170,60,.55) 0%,rgba(120,170,60,.15) 40%,rgba(0,0,0,0) 65%),
             radial-gradient(ellipse at 45% 88%,rgba(255,255,255,.9) 0%,rgba(255,255,255,0) 35%)}
.logo{position:absolute;display:flex;align-items:center;gap:10px;font-family:"Montserrat",Arial,sans-serif;font-weight:700;letter-spacing:.5px;white-space:nowrap}
.logo-mark{width:26px;height:26px;background:currentColor}
.logo--header{left:160px;top:40px;font-size:20px;color:#555}
.nav{position:absolute;right:160px;top:44px;display:flex;gap:30px;font-family:"Montserrat",Arial,sans-serif;font-size:12px;font-weight:600;color:#555;letter-spacing:.5px}
.nav .active{color:var(--blue)}
.hero-title{position:absolute;left:160px;top:186px;font-family:"Montserrat",Arial,sans-serif;font-weight:800;font-size:54px;line-height:60px;color:#111;text-transform:uppercase;letter-spacing:-.5px}
.btn{position:absolute;left:160px;top:476px;width:168px;height:38px;background:var(--orange);color:var(--white);font-size:11px;font-weight:700;letter-spacing:.8px;display:flex;align-items:center;justify-content:center;text-transform:uppercase}

/* values */
.values{position:absolute;left:0;top:640px;width:1200px;height:440px;background:var(--white)}
.values svg{position:absolute;left:0;top:0}
.value-text{position:absolute;top:255px;width:260px;text-align:center;font-size:12px;line-height:19px;color:var(--grey-text)}
.value-text b{font-weight:700}

/* services */
.services{position:absolute;left:0;top:1080px;width:1200px;height:880px;background:var(--section-grey)}
.logo--services{left:160px;top:76px;font-size:20px;color:#666}
.services-title{position:absolute;left:160px;top:168px;font-family:"Montserrat",Arial,sans-serif;font-weight:800;font-size:40px;line-height:44px;color:var(--blue)}
.card{position:absolute;width:280px;height:320px;background:var(--white)}
.card-img{height:164px}
.card-body{padding:18px 18px 0}
.card h3{font-family:"Montserrat",Arial,sans-serif;font-size:14px;font-weight:700;margin-bottom:10px;color:var(--ink)}
.card p{font-size:12px;line-height:18px;color:var(--grey-text);height:54px;overflow:hidden}
.card .more{display:block;margin-top:14px;font-size:11px;font-weight:700;color:var(--orange);letter-spacing:.5px}

/* footer */
.footer{position:absolute;left:0;top:1960px;width:1200px;height:328px;background:var(--footer);color:#bbb}
.logo--footer{left:50%;transform:translateX(-50%);top:34px;font-size:22px;color:#aaa}
.footer-nav{position:absolute;left:370px;top:124px;width:460px;display:flex;justify-content:space-between;font-family:"Montserrat",Arial,sans-serif;font-size:11px;font-weight:600;color:#aaa}
.footer-nav .active{color:var(--green)}
.footer-rule{position:absolute;left:160px;top:160px;width:880px;height:1px;background:#444}
.footer-col{position:absolute;top:186px;width:170px;font-size:11px;line-height:18px;color:#aaa}
.footer-col h4{font-family:"Montserrat",Arial,sans-serif;font-size:11px;font-weight:700;margin-bottom:6px}
.badge{position:absolute;background:#8a8e94}
</style>
</head>
<body>

<header class="hero">
  <div class="hero-photo" role="img" aria-label="Photo of a potted green plant growing in the shape of a rising chart arrow"></div>
  <div class="logo logo--header"><span class="logo-mark"></span>KR Appraisals</div>
  <nav class="nav">
    <span class="active">HOME</span><span>ABOUT</span><span>SERVICES</span><span>SERVICE NEWS</span><span>CONTACT</span>
  </nav>
  <h1 class="hero-title">Business &amp;<br>Intellectual<br>Property<br>Valuations</h1>
  <a class="btn">Contact us today</a>
</header>

<section class="values">
  <svg width="1200" height="440" viewBox="0 0 1200 440">
    <line x1="292" y1="188" x2="908" y2="188" stroke="#d6d6d6" stroke-width="2"/>
    <circle cx="292" cy="188" r="50" fill="var(--blue)"/>
    <circle cx="600" cy="188" r="50" fill="var(--orange)"/>
    <circle cx="908" cy="188" r="50" fill="var(--green)"/>
    <g font-family="Montserrat, Arial, sans-serif" font-size="12" font-weight="700" fill="#fff" text-anchor="middle">
      <text x="292" y="192">TRUST</text>
      <text x="600" y="192">SERVICES</text>
      <text x="908" y="192">EXPERTISE</text>
    </g>
  </svg>
  <p class="value-text" style="left:162px"><b style="color:var(--blue)">Trust</b> is paramount. Clients rely on KR Appraisals for independent, transparent and defensible opinions of value.</p>
  <p class="value-text" style="left:470px"><b style="color:var(--orange)">Service</b> is at the heart of KR Appraisals. We consider the needs of all stakeholders and the specific needs of each engagement.</p>
  <p class="value-text" style="left:778px"><b style="color:var(--green)">Expertise</b> is core to the philosophy of KR Appraisals. Our people remain at the forefront of practice in valuation.</p>
</section>

<section class="services">
  <div class="logo logo--services"><span class="logo-mark"></span>KR Appraisals</div>
  <h2 class="services-title">OUR<br>SERVICES</h2>

  <article class="card" style="left:460px;top:88px">
    <div class="card-img" role="img" aria-label="Photo of financial charts under a magnifying glass" style="background:linear-gradient(135deg,#cfe0f1,#85acd3 60%,#3277b5)"></div>
    <div class="card-body"><h3>Business Valuation</h3><p>Providing independent views on the value of businesses, shares and interests for owners, boards and advisors.</p><span class="more">READ MORE →</span></div>
  </article>
  <article class="card" style="left:760px;top:88px">
    <div class="card-img" role="img" aria-label="Photo of a hand touching digital technology icons" style="background:linear-gradient(135deg,#1f4f86,#3277b5 55%,#85acd3)"></div>
    <div class="card-body"><h3>Intellectual Property Valuation</h3><p>Valuing patents, trademarks, software, customer relationships and other intangible assets with care.</p><span class="more">READ MORE →</span></div>
  </article>
  <article class="card" style="left:160px;top:440px">
    <div class="card-img" role="img" aria-label="Photo of business colleagues in a meeting" style="background:linear-gradient(135deg,#c9b9a6,#8f8a84 55%,#5d5f63)"></div>
    <div class="card-body"><h3>PPA Advisory</h3><p>Through our international network we support companies with purchase price allocation reporting.</p><span class="more">READ MORE →</span></div>
  </article>
  <article class="card" style="left:460px;top:440px">
    <div class="card-img" role="img" aria-label="Photo of a team reviewing a business plan at a desk" style="background:linear-gradient(135deg,#7a6d62,#b7a894 50%,#e2ddd4)"></div>
    <div class="card-body"><h3>Business Plan Coaching</h3><p>Sharp reviews of assumptions, forecasting and key drivers of value for your business plan.</p><span class="more">READ MORE →</span></div>
  </article>
  <article class="card" style="left:760px;top:440px">
    <div class="card-img" role="img" aria-label="Photo of advisors discussing figures on a laptop" style="background:linear-gradient(135deg,#a9b4bf,#6c7a88 55%,#3b4552)"></div>
    <div class="card-body"><h3>Purchase Price Allocation</h3><p>All purchase price allocation reports are prepared to standards auditors and tax authorities expect.</p><span class="more">READ MORE →</span></div>
  </article>
</section>

<footer class="footer">
  <div class="logo logo--footer"><span class="logo-mark"></span>KR Appraisals</div>
  <nav class="footer-nav">
    <span class="active">HOME</span><span>ABOUT</span><span>SERVICES</span><span>SERVICE NEWS</span><span>CONTACT</span>
  </nav>
  <div class="footer-rule"></div>
  <div class="footer-col" style="left:160px"><h4 style="color:var(--green)">CREDITS</h4>© KR Appraisals<br>Design by Lena Brandt<br>Photos by Stock Library</div>
  <div class="footer-col" style="left:380px"><h4 style="color:var(--orange)">LONDON</h4>Harbour Lane 12<br>EC2 4XY London<br>020 555 0184</div>
  <div class="footer-col" style="left:600px"><h4 style="color:var(--green)">AMSTERDAM</h4>Canal Street 48<br>1017 AB Amsterdam<br>020 555 0296</div>
  <div class="badge" style="left:860px;top:186px;width:34px;height:34px;border-radius:50%"></div>
  <div class="badge" style="left:904px;top:194px;width:120px;height:18px"></div>
  <div class="badge" style="left:864px;top:240px;width:130px;height:40px"></div>
</footer>

</body>
</html>
```